Web Design job: SaaS start-up needs a cutting-edge web design

What's Needed:
- All designs files created
- Fully coded implementation in HTML/CSS/Bootstrap
- Pages: 5 -- see content here http://www.TeamVerdexa.com
-- Home Page
-- The Hidden Value
-- Benefits
-- About us
-- Careers
- The existing site has the textual content for each page. We can tweak to meet specific designs if needed.
- You will need to update/create image and interactive content for pages.

Reference:
Our existing website has a lot of content on it for reference -
http://www.TeamVerdexa.com

Description:
We need a web design that focuses in the UX and conveys the idea of magically fixing company problems by way of using our software.

Home Page
The main goal is to Drive Sales of the SaaS tool. When a visitor lands on our home page they should see: What we do, How we can help their problem and How to contact us.
1. Quickly understand What We Do
-- we sell SaaS software.
-- Need to quickly convey what our software does. It's seems complicated but really its not. See the description in about us for more info and visit our existing site.

2. How we can help their problem
-- We aim to solve any problem related to employees
-- Even if the visitor does not have a specific problem in mind, there are several areas organizations can always improve: (some examples below)
---- Create Stronger, More Productive Teams
---- Build Better Communications Pathways
---- Encourage Innovation and Positive Change
---- Develop and Retain Strong "Company Culture"

3. Be able to Contact Us to get started
-- contacting us to get a sales lead is the ultimate goal.
-- the user should not have to hunt to contact us. needs to be easy.

Other Pages (Hidden Value, Benefit, About Us, Careers):
-- These are informative pages about our software and process.
-- If we grab the attention of the user on the home page then these are the pages that they will explore for more info.
-- Should be able to link to these pages from the main nav or from sections with the homepage. For example: What We Do sections could link to the benefits page. How we help their problem sections could link to the Hidden Value page. Regardless of what links to where, the idea is that we will be able to nav to other areas.

About Us:
Our company name is TeamVerdexa (as in Organizational Analysis). We provide a software as a service (SaaS) that uses a simple 6-question survey to analyze the relationships of people within an Organization and provide leaders with ground-breaking Insights about their teams, interactive social network data visualizations to explore their team's composition and we give detailed profiles of the key players (i.e, who are the Social Bridges, Who are the Knowledge Bottlenecks, Who are the Best Mentors, Who are the people that are completely disconnected/out of the loop). Leaders then use this information to make high level organizational decisions.

What's unique about our software:
-- Powerful analysis results from just a 6-question "pulse-surveys"
-- Innovative Tools for visually exploring the organization through relationships as opposed to org-chart
-- Get real-time results as opposed to waiting months with traditional methods
-- Traditional Org-charts represent the organization's skeleton, whereas we uncover the organization's neural network (how it solves problems).

Preferred fonts (but could be convinced otherwise if looks great):
-- Section titles - Aleo
-- Main body - Lato
-- TeamVerdexa logo - Philosopher

Things we like:
-- We like a big slider as the top of the landing page.

Colors to include:
-- Colors in the logo (red, blue, green, teal) as accent colors

Feel of the site:
-- Cutting-edge Software
-- Professional
-- Social Network flare (we analyze relationships)

Note:
If we find a great match with a designer there is strong possibility to continue the relationship with follow on work redesigning our web-based application.

Target Market(s)

Current customers are Morrow Pike & Fenwell, Clearbrook Valley Bank.
We target anyone that manages a large team. Such as Corporate Leaders, High Level Managers, HR Leaders

Industry/Entity Type

Business Software

Contact Information for Business Card

Logo image
Name of company "TEAMVERDEXA" In Philosopher font.
Tagline: "Unlock the Hidden Value In Your Teams"
Person's Name, Title, email, phone.

Coding

Coded - Design and coding required

Number of Pages Required

4 page

Font styles to use
Other font styles liked:
• Lato, Philosopher, Aero

Colors
ec1f27
0255a3

Requirements
Must have
• See description.
Nice to have
• Things we like:
• We like a big slider as the top of the landing page. Ours is a little clunky and outdated but something fresh and sleek would be great.
• Colors to include:
• We would like to use the colors in the logo as accent colors in the site to give a consistent look and feel.
• Feel of the site:
• Cutting-edge Software
• Professional
• Social Network flare (we analyze relationships)

```html
<!DOCTYPE html>
<html lang="en">
<head>
<meta charset="utf-8">
<title>TeamVerdexa – Employee Relationships Define Company Success</title>
<link rel="stylesheet" href="https://fonts.googleapis.com/css2?family=Montserrat:wght@400;500;600&family=Open+Sans:wght@400;600&display=swap">
<style>
  :root {
    --blue: #0255a3;
    --red: #ec1f27;
    --ink: #222428;
    --body: #6a6d72;
    --line: #d4d6d9;
    --panel: #efefef;
    --white: #ffffff;
  }
  * { box-sizing: border-box; margin: 0; padding: 0; }
  html, body { width: 1200px; height: 2936px; overflow: hidden; }
  body { position: relative; background: var(--white); font-family: "Open Sans", Arial, sans-serif; color: var(--body); }

  /* header */
  .site-header { position: absolute; left: 0; top: 0; width: 1200px; height: 135px; background: var(--white); }
  .brand { position: absolute; left: 112px; top: 82px; font-family: "Montserrat", Arial, sans-serif; font-weight: 500; font-size: 17px; letter-spacing: 1px; color: var(--blue); }
  .brand-dot { position: absolute; left: 158px; top: 32px; width: 30px; height: 30px; border-radius: 50%; background: var(--blue); }
  .main-nav a { position: absolute; top: 70px; font-family: "Montserrat", Arial, sans-serif; font-weight: 500; font-size: 12px; color: var(--ink); text-decoration: none; letter-spacing: .3px; }
  .main-nav a.active { color: var(--blue); }
  .home-icon { position: absolute; left: 604px; top: 48px; }

  /* hero slider */
  .hero { position: absolute; left: 0; top: 135px; width: 1200px; height: 571px; overflow: hidden; }
  .hero-photo { position: absolute; inset: 0; background: linear-gradient(100deg, #c9d2d6 0%, #e9eef0 35%, #a9c9cf 65%, #5f9aa3 100%); }
  .hero-title { position: absolute; left: 507px; top: 200px; font-family: "Montserrat", Arial, sans-serif; font-weight: 400; font-size: 46px; line-height: 59px; color: var(--ink); }
  .slider-dots { position: absolute; left: 565px; top: 535px; display: flex; gap: 9px; }
  .slider-dots span { width: 9px; height: 9px; border-radius: 50%; background: #f0b4b6; }
  .slider-dots span.on { background: var(--red); }

  /* section titles */
  .section-title { position: absolute; left: 0; width: 1200px; text-align: center; font-family: "Montserrat", Arial, sans-serif; font-weight: 500; font-size: 29px; color: var(--ink); }
  .intro { position: absolute; left: 124px; top: 864px; width: 952px; text-align: center; font-size: 11px; line-height: 29px; color: var(--body); }

  /* features */
  .feature-graphic { position: absolute; left: 440px; top: 1048px; width: 320px; height: 385px; border-radius: 12px; background: linear-gradient(135deg, #eef0f2 0%, #f7f7f8 45%, #e8eef5 100%); }
  .feature { position: absolute; width: 282px; }
  .feature.left { text-align: right; }
  .feature h3 { font-family: "Montserrat", Arial, sans-serif; font-weight: 500; font-size: 20px; line-height: 25px; color: var(--ink); margin-bottom: 6px; }
  .feature p { font-size: 11px; line-height: 29px; color: var(--body); }

  /* help */
  .help { position: absolute; left: 0; top: 1556px; width: 1200px; height: 514px; background: var(--panel); }
  .help-item { position: absolute; width: 240px; text-align: center; }
  .help-badge { width: 124px; height: 124px; margin: 0 auto; border-radius: 50%; border: 2px solid var(--blue); padding: 5px; }
  .help-badge div { width: 100%; height: 100%; border-radius: 50%; background: var(--blue); display: flex; align-items: center; justify-content: center; }
  .help-item p { margin-top: 20px; font-size: 12px; line-height: 26px; font-weight: 600; color: #44474c; }

  /* contact */
  .contact-item { position: absolute; top: 2225px; display: flex; align-items: center; gap: 14px; font-size: 11px; color: #44474c; }
  .contact-icon { width: 60px; height: 60px; border-radius: 50%; background: var(--blue); display: flex; align-items: center; justify-content: center; }
  .form-title { position: absolute; left: 0; top: 2338px; width: 1200px; text-align: center; font-family: "Montserrat", Arial, sans-serif; font-weight: 500; font-size: 20px; color: var(--ink); letter-spacing: .5px; }
  .field { position: absolute; border: 1px solid var(--line); background: var(--white); padding: 0 18px; font-size: 11px; color: #55585c; display: flex; align-items: center; }
  .field.area { align-items: flex-start; padding-top: 20px; }
  .submit { position: absolute; left: 524px; top: 2681px; width: 153px; height: 53px; border: 1.5px solid var(--red); color: var(--red); font-family: "Montserrat", Arial, sans-serif; font-size: 13px; display: flex; align-items: center; justify-content: center; background: var(--white); }

  /* footer */
  .site-footer { position: absolute; left: 0; top: 2812px; width: 1200px; height: 124px; background: var(--panel); font-size: 11px; color: #55585c; }
  .footer-links { position: absolute; left: 112px; top: 40px; }
  .copyright { position: absolute; left: 112px; top: 74px; }
  .social { position: absolute; top: 50px; width: 24px; height: 24px; border-radius: 50%; background: #a5a7aa; }
</style>
</head>
<body>

<header class="site-header">
  <span class="brand-dot"></span>
  <div class="brand">TEAMVERDEXA</div>
  <nav class="main-nav">
    <svg class="home-icon" width="16" height="14" viewBox="0 0 16 14"><path d="M8 0 0 7h2v7h4V9h4v5h4V7h2z" fill="#0255a3"/></svg>
    <a class="active" style="left:596px">HOME</a>
    <a style="left:684px">ABOUT US</a>
    <a style="left:797px">SERVICES</a>
    <a style="left:902px">CAREERS</a>
    <a style="left:1007px">CLIENT LOGIN</a>
  </nav>
</header>

<section class="hero">
  <div class="hero-photo" role="img" aria-label="Laptop on a desk showing a colourful social network graph, with a tablet and phone beside it in a bright office"></div>
  <h1 class="hero-title">Employee Relationships<br>Define Company Success</h1>
  <div class="slider-dots"><span></span><span></span><span class="on"></span><span></span></div>
</section>

<h2 class="section-title" style="top:806px">WHAT WE DO</h2>
<p class="intro">Our company name is TeamVerdexa (as in Organizational Analysis). We provide a software as a service (SaaS) that uses a simple 6-question survey to analyze the relationships of people within an Organization and provide leaders with ground-breaking Insights about their teams, interactive social network data visualizations to explore their team's composition and we give detailed profiles of the key players (i.e, who are the Social Bridges, Who are the Knowledge Bottlenecks, Who are the Best Mentors, Who are the people that are completely disconnected/out of the loop). Leaders then use this information to make high level organizational decisions.</p>

<div class="feature-graphic" role="img" aria-label="Four service illustrations — survey clipboard, algorithms, team insights, expert review — framed by grey curved swooshes"></div>

<div class="feature left" style="left:141px;top:1097px"><h3>ON-LINE PULSE SURVEY</h3><p>FIRST Data-Driven Platform with Innovative Tools for Dynamic, Real-Time Analyses and Exploration of Employee Relationships</p></div>
<div class="feature" style="left:808px;top:1097px"><h3>PROPRIETARY ALGORITHMS</h3><p>FIRST Data-Driven Platform with Innovative Tools for Dynamic, Real-Time Analyses and Exploration of Employee Relationships</p></div>
<div class="feature left" style="left:141px;top:1294px"><h3>ORGANIZATIONAL KEY INSIGHTS</h3><p>FIRST Data-Driven Platform with Innovative Tools for Dynamic, Real-Time Analyses and Exploration of Employee Relationships</p></div>
<div class="feature" style="left:808px;top:1287px"><h3>EXPERT REVIEW AND ACTION<br>PLANS</h3><p>FIRST Data-Driven Platform with Innovative Tools for Dynamic, Real-Time Analyses and Exploration of Employee Relationships</p></div>

<section class="help">
  <h2 class="section-title" style="top:112px">HOW WE CAN HELP THEIR PROBLEM</h2>
  <div class="help-item" style="left:103px;top:222px">
    <div class="help-badge"><div><svg width="34" height="40" viewBox="0 0 34 40"><path d="M17 2 3 7v11c0 10 6 17 14 20 8-3 14-10 14-20V7z" fill="none" stroke="#fff" stroke-width="3.5"/><path d="M17 6v28c-6-3-10-8-10-16V10z" fill="#fff"/></svg></div></div>
    <p>Create Stronger, More Productive<br>Teams</p>
  </div>
  <div class="help-item" style="left:354px;top:222px">
    <div class="help-badge"><div><svg width="44" height="40" viewBox="0 0 44 40"><path d="M14 2h26v20H30l-6 6v-6H14z" fill="#fff"/><path d="M4 12h18v18h-8l-6 6v-6H4z" fill="#fff" stroke="#0255a3" stroke-width="2"/><path d="M8 19h10M8 24h10" stroke="#0255a3" stroke-width="2"/></svg></div></div>
    <p>Build Better Communications<br>Pathways</p>
  </div>
  <div class="help-item" style="left:604px;top:222px">
    <div class="help-badge"><div><svg width="36" height="44" viewBox="0 0 36 44"><path d="M6 10a16 16 0 0 1 24 0M10 14a10 10 0 0 1 16 0" fill="none" stroke="#fff" stroke-width="3"/><circle cx="18" cy="20" r="4" fill="#fff"/><rect x="11" y="27" width="14" height="15" rx="2" fill="#fff"/></svg></div></div>
    <p>Encourage Innovation and<br>Positive Change</p>
  </div>
  <div class="help-item" style="left:855px;top:222px">
    <div class="help-badge"><div><svg width="40" height="40" viewBox="0 0 40 40"><path d="M4 4h32v24H16l-8 8v-8H4z" fill="#fff"/><path d="M13 16h4v9h-4zM19 25v-9l4-7c2 0 3 1 3 3l-1 4h5c1 0 2 1 2 2l-2 7H19z" fill="#0255a3"/></svg></div></div>
    <p>Develop and Retain Strong<br>" Company Culture"</p>
  </div>
</section>

<h2 class="section-title" style="top:2150px">HOW TO CONTACT US</h2>
<div class="contact-item" style="left:266px"><div class="contact-icon"><svg width="16" height="22" viewBox="0 0 16 22"><path d="M8 0a8 8 0 0 0-8 8c0 6 8 14 8 14s8-8 8-14a8 8 0 0 0-8-8z" fill="#fff"/><circle cx="8" cy="8" r="3" fill="#0255a3"/></svg></div><span>Millbrook, AL</span></div>
<div class="contact-item" style="left:496px"><div class="contact-icon"><svg width="20" height="20" viewBox="0 0 20 20"><path d="M4 1l4 4-2 3c1 3 3 5 6 6l3-2 4 4-3 3C8 19 1 12 1 4z" fill="#fff"/></svg></div><span>555-014-2290</span></div>
<div class="contact-item" style="left:720px"><div class="contact-icon"><svg width="20" height="15" viewBox="0 0 20 15"><rect width="20" height="15" rx="1" fill="#fff"/><path d="M0 1l10 7 10-7" fill="none" stroke="#0255a3" stroke-width="1.6"/></svg></div><span>hello@teamverdexa.com</span></div>

<h3 class="form-title">SEND US A MESSAGE</h3>
<div class="field" style="left:112px;top:2409px;width:473px;height:53px">Name</div>
<div class="field" style="left:612px;top:2409px;width:474px;height:53px">Email Address</div>
<div class="field" style="left:112px;top:2480px;width:473px;height:53px">Phone</div>
<div class="field" style="left:612px;top:2480px;width:474px;height:53px">Subject</div>
<div class="field area" style="left:112px;top:2552px;width:974px;height:92px">Message</div>
<div class="submit">SUBMIT</div>

<footer class="site-footer">
  <div class="footer-links">Privacy Policy &nbsp;|&nbsp; Sitemap</div>
  <div class="copyright">© 2016 TeamVerdexa. All Rights Reserved.</div>
  <span class="social" style="left:1031px"></span>
  <span class="social" style="left:1062px"></span>
</footer>

</body>
</html>
```